Business Cards for new orthopaedic surgery practice

My husband and I are starting our own orthopaedic surgery practice. We are looking for a business card that is uniform, but one will have my name/title and the other will have his. You can just create one design with my name on it for now. But when I choose your design as the winning design I will ask that you add another copy with his name/title.

We are looking for classy, simple, elite all in one. We like dark blues/a little gold/yellow. Something that goes with our logo. We want our logo incorporated. Here is all the info you need:
Business name: RV Bone & Vitality Center
Location: 38517 North Willowmere Ave
Coral Springs, FL 33071
Phone: 954-218-4063
Fax: 954-582-7341
Email: info@myrvbonecare.example

Names: Lydia Vance, M.D.
Board Certified Hand and Upper Extremity Surgeon

Ebo Dansu, M.D.
Board Certified Hip & Knee Replacement/General Orthopaedic Surgeon

Can decide what you want to put on the back. Maybe a slogan:
Rooted in Care. Focused on You

I am just going to upload our logo. The only thing is if we select you as the winning design, the location, and phone numbers may change. We will need your help to update that once fully solidified.

Industry/Entity Type

Medical

Contact Information for Business Card

Colors
0054AA
0677BA
7BADD7
CADEEF
E8F1F8
0094D4
00A9DD
6FCCEA
C7EBF8
E9F6FB

Requirements
Must have
• class, appeal,
Should not have
• We want to air on the side of masculine if we are looking at masculine vs. feminine feel. But we still want it classy, sophisticated, and something we will love

```html
<!DOCTYPE html>
<html lang="en">
<head>
<meta charset="utf-8">
<title>RV Bone &amp; Vitality Center – Business Card</title>
<link href="https://fonts.googleapis.com/css2?family=Montserrat:wght@400;600&display=swap" rel="stylesheet">
<style>
  :root {
    --navy: #1c2b4f;
    --navy-text: #1b2440;
    --gold: #c39a5a;
    --paper: #ffffff;
    --backdrop: #e9ebef;
    --on-navy: #ffffff;
  }
  * { margin: 0; padding: 0; box-sizing: border-box; }
  html, body {
    width: 1200px; height: 897px; overflow: hidden;
    background: var(--backdrop);
    font-family: "Montserrat", sans-serif;
  }
  .card {
    position: absolute;
    left: 303px; width: 595px; height: 338px;
    border-radius: 22px;
    overflow: hidden;
  }
  .card--front { top: 92px; background: var(--paper); }
  .card--back { top: 470px; background: var(--navy); }

  .brand {
    position: absolute;
    display: flex; flex-direction: column; align-items: center; justify-content: center;
    text-align: center;
  }
  .brand__ring {
    position: absolute; inset: 0;
    border-radius: 50%;
    border: 2px solid var(--gold);
  }
  .brand__name {
    position: relative;
    font-weight: 600;
    letter-spacing: 2px;
    text-transform: uppercase;
    line-height: 1.35;
  }
  .card--front .brand { left: 37px; top: 76px; width: 184px; height: 184px; }
  .card--front .brand__name { color: var(--navy-text); font-size: 14px; }
  .card--back .brand { left: 165px; top: 36px; width: 264px; height: 264px; }
  .card--back .brand__name { color: var(--on-navy); font-size: 20px; }

  .details { position: absolute; left: 315px; top: 0; right: 0; color: var(--navy-text); }
  .details__name {
    position: absolute; top: 27px; left: 0;
    font-size: 25px; font-weight: 600; color: var(--gold);
    letter-spacing: 0.5px; white-space: nowrap;
  }
  .details__title {
    position: absolute; top: 55px; left: 0;
    font-size: 14px; line-height: 17px;
  }
  .details__rule {
    position: absolute; top: 103px; left: 0; right: 0;
    height: 1.5px; background: var(--gold);
  }
  .contact {
    position: absolute; top: 193px; left: 0;
    list-style: none; font-size: 14px; line-height: 17px;
  }
  .contact li { display: flex; align-items: center; gap: 6px; }
  .contact svg { width: 11px; height: 11px; flex: none; }
  .contact .accent { color: var(--gold); }
  .address {
    position: absolute; top: 274px; left: 0;
    font-size: 14px; line-height: 17px; font-style: normal;
  }
</style>
</head>
<body>

<section class="card card--front">
  <div class="brand">
    <span class="brand__ring"></span>
    <span class="brand__name">RV Bone &amp;<br>Vitality<br>Center</span>
  </div>

  <div class="details">
    <h1 class="details__name">LYDIA VANCE, M.D</h1>
    <p class="details__title">Board Certified Hand and<br>Upper Extremity Surgeon</p>
    <div class="details__rule"></div>

    <ul class="contact">
      <li>
        <svg viewBox="0 0 12 12" aria-hidden="true"><path d="M2.5 1 4.5 1 5.3 3.4 4 4.3C4.7 5.9 6.1 7.3 7.7 8L8.6 6.7 11 7.5 11 9.5C11 10.3 10.3 11 9.5 11 5 11 1 7 1 2.5 1 1.7 1.7 1 2.5 1Z" fill="var(--gold)"/></svg>
        954-218-4063
      </li>
      <li>
        <svg viewBox="0 0 12 12" aria-hidden="true"><g fill="none" stroke="var(--gold)" stroke-width="1"><rect x="3" y="1" width="6" height="3"/><rect x="1" y="4" width="10" height="5"/><rect x="3" y="7" width="6" height="4"/></g></svg>
        954-582-7341
      </li>
      <li>
        <svg viewBox="0 0 12 12" aria-hidden="true"><g fill="none" stroke="var(--gold)" stroke-width="1"><rect x="1" y="2.5" width="10" height="7"/><path d="M1 2.5 6 6.5 11 2.5"/></g></svg>
        info@myrvbonecare.example
      </li>
      <li>
        <svg viewBox="0 0 12 12" aria-hidden="true"><g fill="none" stroke="var(--gold)" stroke-width="1"><circle cx="6" cy="6" r="5"/><ellipse cx="6" cy="6" rx="2.2" ry="5"/><path d="M1 6H11M2 3.5H10M2 8.5H10"/></g></svg>
        <span>www.<span class="accent">myrvbonecare</span>.example</span>
      </li>
    </ul>

    <address class="address">38517 North Willowmere Ave<br>Maple Hollow,FL 33219</address>
  </div>
</section>

<section class="card card--back">
  <div class="brand">
    <span class="brand__name">RV Bone &amp;<br>Vitality<br>Center</span>
  </div>
</section>

</body>
</html>
```